Navoro & Omvar Automotive Repair Shop. Need a new website design.

We specialize in Navoro & Omvar auto repair, but also work on other Asian import vehicles. We have been in business for 7 years and pride ourselves on high quality auto repair that is fixed right the first time. Would like the automotive repair website to incorporate the colors black, red and white if possible and have our logo and some Navoro and Omvar vehicles included in the website.

Target Market(s)

Navoro & Omvar vehicle owners

Industry/Entity Type

Automotive Repair

Coding

Coded - Design and coding required

Number of Pages Required

5+ page

Colors
EB3D1F
EC4F4E
F09395
F8D3D4
FCEDEE

Requirements
Must have
• Home, Services, Contact Us, Schedule appointment, and a gallery tab that I can add shop pictures to when completed.
Nice to have
• Would like to see example pictures of job next to each service listed.
Should not have
• Service not related to auto repair. Ex. auto detailing, towing, car wash

```html
<!DOCTYPE html>
<html lang="en">
<head>
<meta charset="utf-8">
<title>Kestrel Automotive – Navoro &amp; Omvar Auto Repair</title>
<link rel="stylesheet" href="https://fonts.googleapis.com/css2?family=Krona+One&family=Barlow:wght@400;500;600;700&display=swap">
<style>
:root{
  --red:#e3121b;
  --red-deep:#b80d14;
  --black:#000;
  --ink:#0a0a0a;
  --panel:#111;
  --grey:#2a2a2a;
  --line:#444;
  --white:#fff;
  --muted:#cfcfcf;
  --display:'Krona One',sans-serif;
  --body:'Barlow',sans-serif;
}
*{box-sizing:border-box;margin:0;padding:0}
html,body{width:1200px;height:4612px;overflow:hidden}
body{position:relative;background:var(--ink);color:var(--white);font-family:var(--body)}
.abs{position:absolute}
a{color:inherit;text-decoration:none}

.hero-bg{left:0;top:0;width:1200px;height:790px;background:linear-gradient(90deg,#141414 0%,#1b1b1b 40%,#0e0e0e 100%)}
.hero-photo{left:430px;top:0;width:770px;height:760px;background:radial-gradient(ellipse at 60% 45%,#9a9a9a 0%,#5a5a5a 30%,#2a2a2a 60%,rgba(20,20,20,0) 80%)}
.hero-band{left:0;top:660px;width:1200px;height:140px}
.about-bg{left:0;top:790px;width:1200px;height:750px;background:#050505}
.services-bg{left:0;top:1540px;width:1200px;height:700px;background:linear-gradient(180deg,#1c1c1c,#232323 60%,#1a1a1a)}
.gallery-bg{left:0;top:2222px;width:1200px;height:870px;background:linear-gradient(180deg,#2a2a2a 0%,#141414 40%,#0c0c0c 100%)}
.chevron{left:0;top:2215px;width:1200px;height:150px}
.makes-bg{left:0;top:3090px;width:1200px;height:662px;background:#000}
.contact-bg{left:0;top:3752px;width:1200px;height:560px;background:linear-gradient(90deg,#0d0d0d 0%,#141414 55%,#262626 100%)}
.footer-bg{left:0;top:4300px;width:1200px;height:312px;background:#050505}
.footer-band{left:0;top:4250px;width:1200px;height:150px}

.logo{display:flex;align-items:center;gap:10px;font-family:var(--display);font-size:24px;color:var(--white)}
.logo .mark{width:16px;height:16px;background:var(--red)}
.nav{left:366px;top:48px;font-size:13px;font-weight:500;letter-spacing:.3px}
.nav a{position:absolute;white-space:nowrap}
.nav .current::after{content:"";position:absolute;left:0;right:0;top:24px;height:2px;background:var(--red)}
.btn-outline{border:1px solid var(--white);font-size:11px;font-weight:600;display:flex;align-items:center;justify-content:center;letter-spacing:.3px}

.hero-frame{left:124px;top:247px;width:230px;height:367px;border:4px solid #d8d8d8;border-right:none}
.hero-title{left:172px;top:290px;font-family:var(--display);font-size:29px;line-height:41px;letter-spacing:.3px;white-space:nowrap}
.hero-title .accent{color:var(--red)}
.hero-text{left:172px;top:420px;width:390px;font-size:15px;line-height:21px;color:#e4e4e4}
.btn-red{background:var(--red);color:var(--white);font-weight:700;display:flex;align-items:center;justify-content:center;font-size:14px;letter-spacing:.3px}

.corner-red{left:104px;top:841px;width:130px;height:52px;background:var(--red)}
.about-photo{left:113px;top:853px;width:444px;height:427px;background:linear-gradient(160deg,#5b5f66,#2e3238 55%,#1b1d20)}
.engine-art{left:59px;top:1110px;width:245px;height:206px;border-radius:40%;background:radial-gradient(circle,#9a9a9a 0%,#555 45%,rgba(5,5,5,0) 72%)}
.exp-badge{left:458px;top:1164px;width:128px;height:113px;background:var(--red);text-align:center;padding-top:14px}
.exp-badge .num{font-family:var(--display);font-size:36px;line-height:40px}
.exp-badge .lbl{font-size:14px;font-weight:600;line-height:17px}
.eyebrow{color:var(--red);font-size:13px;letter-spacing:1px;text-transform:uppercase}
.h2{font-family:var(--display);font-size:30px;letter-spacing:.3px;line-height:40px;white-space:nowrap}
.about-rule{left:1012px;top:892px;width:10px;height:6px;background:var(--red)}
.about-lead{left:612px;top:933px;width:520px;font-size:15.5px;font-weight:600;line-height:23px}
.about-body{left:612px;top:1019px;width:520px;font-size:14px;line-height:23px;color:#d6d6d6}
.btn-line-red{left:620px;top:1230px;width:164px;height:45px;border:2px solid var(--red);color:var(--red);font-size:12px;letter-spacing:2px;display:flex;align-items:center;justify-content:center;font-weight:600}

.auth-corner-tl{left:104px;top:1356px;width:95px;height:60px;border-left:4px solid #555;border-top:4px solid #555}
.auth-corner-br{left:1020px;top:1558px;width:54px;height:64px;border-right:4px solid #555;border-bottom:4px solid #555}
.auth-box{left:111px;top:1361px;width:908px;height:256px;background:#0c0c0c;border:1px solid #3a3a3a}
.auth-title{left:111px;top:1405px;width:908px;text-align:center;font-family:var(--display);font-size:16px;line-height:25px;letter-spacing:.5px}
.badge{position:absolute}

.center-head{left:0;width:1200px;text-align:center}
.svc-col{display:flex;flex-direction:column;gap:24px}
.svc{position:relative;font-size:15px;line-height:22px}
.svc::before{content:"";position:absolute;left:-44px;top:-3px;width:24px;height:24px;border:2px solid #e0e0e0;border-radius:50%}
.svc::after{content:"";position:absolute;left:-36px;top:5px;width:8px;height:8px;background:#e0e0e0;border-radius:50%}
.svc-active{left:97px;top:1787px;width:285px;height:54px;background:var(--red);clip-path:polygon(0 0,100% 0,94% 100%,0 100%)}

.shot{background:linear-gradient(150deg,#6a6e74,#34383d 60%,#1d1f22)}

.makes-title{left:0;top:3160px;width:1200px;text-align:center;font-family:var(--display);font-size:20px;line-height:25px;letter-spacing:.5px}
.makes-grid{left:131px;top:3283px;width:920px;display:grid;grid-template-columns:repeat(4,1fr);border-top:1px solid var(--line);border-left:1px solid var(--line)}
.make{height:144px;border-right:1px solid var(--line);border-bottom:1px solid var(--line);display:flex;align-items:center;justify-content:center;gap:10px;font-size:22px;font-weight:600;letter-spacing:2px;text-transform:uppercase}
.make .dot{width:12px;height:12px;border-radius:50%;border:2px solid var(--white)}
.make.highlight{background:linear-gradient(135deg,#e6e6e6,#9c9c9c 55%,#d4d4d4);color:#111}
.make.highlight .dot{border-color:#111}

.contact-rule{left:50px;top:3946px;width:60px;height:3px;background:var(--red)}
.contact-text{left:136px;top:3987px;width:390px;font-size:14.5px;line-height:27px;color:#ddd}
.form-box{left:595px;top:3838px;width:490px;height:346px;border:1px solid #555;background:rgba(10,10,10,.85)}
.form-title{left:637px;top:3876px;font-family:var(--display);font-size:15px;letter-spacing:1px}
.field{border:1px solid #bbb;font-size:10px;padding:9px 14px;color:#eee}

.foot-nav{top:4450px;font-size:16px;font-weight:700;letter-spacing:.5px}
.foot-dot{top:4458px;width:5px;height:5px;background:var(--red);border-radius:50%}
.social{top:4545px;font-size:13px;font-weight:600;display:flex;gap:18px}
</style>
</head>
<body>

<div class="abs hero-bg"></div>
<div class="abs hero-photo" role="img" aria-label="Mechanic's hands working on an exposed engine block with camshafts and timing gears"></div>
<svg class="abs hero-band" viewBox="0 0 1200 140" preserveAspectRatio="none" aria-hidden="true">
  <polygon points="0,100 600,0 1200,100 1200,140 0,140" fill="#050505"/>
  <polygon points="0,100 600,0 1200,100 1200,122 600,36 0,130" fill="#e3121b"/>
</svg>

<header>
  <a class="abs logo" style="left:136px;top:62px" href="#">KESTREL<span class="mark"></span></a>
  <nav class="abs nav" aria-label="Main">
    <a class="current" style="left:0;top:0">HOME</a>
    <a style="left:86px;top:0">ABOUT US</a>
    <a style="left:196px;top:0">OUR SERVICES</a>
    <a style="left:348px;top:4px">GALLERY</a>
    <a style="left:455px;top:4px">CONTACT</a>
  </nav>
  <a class="abs btn-outline" style="left:921px;top:45px;width:184px;height:34px">FINANCING APPLICATION</a>
</header>

<div class="abs hero-frame"></div>
<h1 class="abs hero-title">SPECIALIZING IN<br>NAVORO AND OMVAR<br><span class="accent">AUTO REPAIR</span></h1>
<p class="abs hero-text">Kestrel Automotive is a locally owned and operated auto repair shop in Brookhaven that offers comprehensive car care and services</p>
<a class="abs btn-red" style="left:172px;top:505px;width:281px;height:54px">SCHEDULE AN APPOINTMENT</a>

<div class="abs about-bg"></div>
<div class="abs corner-red"></div>
<div class="abs about-photo" role="img" aria-label="Technician working under a lifted vehicle in the shop"></div>
<div class="abs engine-art" role="img" aria-label="Line illustration of a V engine"></div>
<div class="abs exp-badge"><div class="num">7</div><div class="lbl">YEARS OF<br>EXPERIENCE</div></div>

<div class="abs eyebrow" style="left:609px;top:855px">Our Company</div>
<h2 class="abs h2" style="left:609px;top:876px">ABOUT KESTREL</h2>
<div class="abs about-rule"></div>
<p class="abs about-lead">Kestrel Automotive is a locally owned and operated auto repair shop in Brookhaven that offers comprehensive car care and services for Navoro &amp; Omvar and all other Asian imports vehicles.</p>
<p class="abs about-body">Led by an NCT master certified technician with 7 years in business serving Navoro &amp; Omvar owners, our auto shop is your go to facility for everything from factory auto maintenance, including oil changes, fluid services and tune ups, to complex engine repairs, hybrid diagnostic &amp; repair, brake jobs, etc. We have state of the art equipment and tools to ensure that we can properly diagnose and repair your vehicle right the first time and get you back on the road quickly. Our work comes with a warranty and we also offer discounts for Rydo &amp; Hoply rides.</p>
<a class="abs btn-line-red">LEARN MORE</a>

<div class="abs services-bg"></div>
<div class="abs auth-corner-tl"></div>
<div class="abs auth-corner-br"></div>
<div class="abs auth-box"></div>
<h3 class="abs auth-title">AUTHORIZED INSTALLER FOR VANTORA OIL,<br>PELLION BATTERY</h3>
<div class="badge" style="left:233px;top:1460px;width:82px;height:112px;background:#fff;border-radius:4px" role="img" aria-label="Certification badge"></div>
<div class="badge" style="left:410px;top:1468px;width:104px;height:104px;border:3px solid #2f8fa0;border-radius:50%" role="img" aria-label="Local award badge"></div>
<div class="badge" style="left:608px;top:1478px;width:140px;height:56px;background:var(--red)" role="img" aria-label="Battery partner badge"></div>
<div class="badge" style="left:823px;top:1496px;width:172px;height:36px;background:var(--red)" role="img" aria-label="Oil partner badge"></div>

<div class="abs eyebrow center-head" style="top:1684px">What We Do</div>
<h2 class="abs h2 center-head" style="top:1704px">SERVICES PROVIDE</h2>

<div class="abs svc-active"></div>
<ul class="abs svc-col" style="left:168px;top:1805px;list-style:none">
  <li class="svc">Oil Changes</li>
  <li class="svc">Computer Diagnostics</li>
  <li class="svc">Electrical Specialists</li>
  <li class="svc">Tires</li>
  <li class="svc">Tire Balance &amp; Rotations</li>
  <li class="svc">Pre Purchase Inspections</li>
  <li class="svc">Insurance Claims</li>
  <li class="svc">Emission Repair &amp; Catalytic<br>Converters</li>
</ul>
<ul class="abs svc-col" style="left:476px;top:1805px;list-style:none">
  <li class="svc">Engine Repair</li>
  <li class="svc">Heating &amp; AC Repair</li>
  <li class="svc">State Inspection</li>
  <li class="svc">Suspension Service &amp; Repair</li>
  <li class="svc">Leveling Kits &amp; Minor Lift Kit installation</li>
  <li class="svc">Brakes Service &amp; Repair</li>
  <li class="svc">Exhaust, Muffler Service &amp; Repair</li>
  <li class="svc">Automatic, Manual, Computerized<br>Transmission Service &amp; Repair</li>
</ul>
<ul class="abs svc-col" style="left:845px;top:1805px;list-style:none">
  <li class="svc">Clutch Service &amp; Repair</li>
  <li class="svc">CV Axle Service &amp; Repair</li>
  <li class="svc">Fuel Injection System Service<br>Cleaning &amp; Repair</li>
  <li class="svc">Timing Belts &amp; Water Pumps</li>
  <li class="svc">Radiators &amp; Fans Service &amp; Repair</li>
  <li class="svc">Tune ups &amp; Factory Scheduled<br>Maintenance</li>
  <li class="svc">Hybrid Vehicle diagnostic &amp; repair<br>24-hr Night Drop</li>
</ul>

<div class="abs gallery-bg"></div>
<svg class="abs chevron" viewBox="0 0 1200 150" preserveAspectRatio="none" aria-hidden="true">
  <polygon points="0,0 1200,0 1200,7 600,130 0,7" fill="#1a1a1a"/>
  <polygon points="0,7 600,130 1200,7 1200,25 600,150 0,25" fill="#9a9a9a"/>
</svg>
<div class="abs eyebrow center-head" style="top:2415px">Photo Gallery</div>
<h2 class="abs h2 center-head" style="top:2436px">OUR GALLERY</h2>
<div class="abs shot" style="left:107px;top:2513px;width:325px;height:236px" role="img" aria-label="Mechanic working on suspension under a vehicle"></div>
<div class="abs shot" style="left:442px;top:2513px;width:323px;height:236px" role="img" aria-label="Omvar SUV engine bay with AC service equipment"></div>
<div class="abs shot" style="left:777px;top:2513px;width:323px;height:236px" role="img" aria-label="Engine partly disassembled for timing repair"></div>
<div class="abs shot" style="left:109px;top:2769px;width:489px;height:236px" role="img" aria-label="Silver Navoro pickup raised on a lift with wheel removed"></div>
<div class="abs shot" style="left:612px;top:2769px;width:488px;height:236px" role="img" aria-label="Customer vehicles parked in front of the shop building"></div>

<div class="abs makes-bg"></div>
<h2 class="abs makes-title">KESTREL AUTOMOTIVE SPECIALIZES IN NAVORO &amp; OMVAR<br>AUTO REPAIR BUT ALSO SERVICE AND REPAIR<br>THE FOLLOWING MAKES</h2>
<div class="abs makes-grid">
  <div class="make"><span class="dot"></span>Arvena</div>
  <div class="make"><span class="dot"></span>Halvex</div>
  <div class="make"><span class="dot"></span>Ilmora</div>
  <div class="make"><span class="dot"></span>Kyro</div>
  <div class="make highlight"><span class="dot"></span>Miretsu</div>
  <div class="make"><span class="dot"></span>Mazelo</div>
  <div class="make"><span class="dot"></span>Nevara</div>
  <div class="make"><span class="dot"></span>Hokiro</div>
</div>
<a class="abs btn-red" style="left:444px;top:3607px;width:292px;height:56px">SCHEDULE AN APPOINTMENT</a>

<div class="abs contact-bg"></div>
<div class="abs eyebrow" style="left:135px;top:3896px">Get In Touch</div>
<div class="abs contact-rule"></div>
<h2 class="abs h2" style="left:135px;top:3922px">CONTACT <span style="color:var(--red)">US</span></h2>
<p class="abs contact-text">Contact us for a free estimate! Please include year, make, and model and the service or repair you would like repair you would like an estimate on.</p>
<a class="abs btn-red" style="left:140px;top:4089px;width:234px;height:42px;font-size:12px">SCHEDULE AN APPOINTMENT</a>

<div class="abs form-box"></div>
<h3 class="abs form-title">LEAVE US A MESSAGE</h3>
<div class="abs field" style="left:636px;top:3917px;width:200px;height:36px">First Name*</div>
<div class="abs field" style="left:845px;top:3917px;width:203px;height:36px">Last Name*</div>
<div class="abs field" style="left:636px;top:3965px;width:200px;height:36px">Email address*</div>
<div class="abs field" style="left:845px;top:3965px;width:203px;height:36px">Phone*</div>
<div class="abs field" style="left:636px;top:4015px;width:412px;height:80px">Message</div>
<a class="abs btn-red" style="left:639px;top:4114px;width:129px;height:34px;font-size:12px;letter-spacing:1px">SUBMIT</a>

<div class="abs footer-bg"></div>
<svg class="abs footer-band" viewBox="0 0 1200 150" preserveAspectRatio="none" aria-hidden="true">
  <polygon points="0,0 1200,0 1200,120 600,14 0,120" fill="#141414"/>
  <polygon points="0,120 600,14 1200,120 1200,150 600,46 0,150" fill="#e3121b"/>
  <polygon points="0,150 600,46 1200,150" fill="#050505"/>
</svg>
<a class="abs logo" style="left:534px;top:4360px">KESTREL<span class="mark"></span></a>

<a class="abs foot-nav" style="left:170px">HOME</a>
<span class="abs foot-dot" style="left:276px"></span>
<a class="abs foot-nav" style="left:330px">ABOUT US</a>
<span class="abs foot-dot" style="left:468px"></span>
<a class="abs foot-nav" style="left:520px">OUR SERVICES</a>
<span class="abs foot-dot" style="left:694px"></span>
<a class="abs foot-nav" style="left:748px">GALLERY</a>
<span class="abs foot-dot" style="left:873px"></span>
<a class="abs foot-nav" style="left:933px">CONTACT</a>

<p class="abs" style="left:168px;top:4512px;font-size:12px">Copyright © 2024 Kestrel Automotive. All rights reserved.</p>
<div class="abs social" style="left:168px">
  <span>Socia</span><span>Chirp</span><span>Linkly</span><span>Snapra</span>
</div>
<div class="abs" style="left:856px;top:4517px;display:flex;align-items:center;gap:8px;font-size:24px;font-weight:700;color:#19b67a">
  <span style="width:18px;height:18px;border-radius:50%;background:#19b67a"></span>Paywell finance
</div>

</body>
</html>
```